Psychiatric Office Needs a Website- 1st Time Ever!

Been in practice since 2003 with no website, but finally ready to dive in. We are Maplecrest Behavioral Healthcare, a mental health outpatient practice based in Fayetteville, Georgia that sees diverse individuals and families from childhood to advanced age for a variety of conditions. We've grown by word of mouth and referral but would now like to have a digital footprint. Be the pioneer of our website and we will be sure to share. We would like to see designs that are modern, animated, fairly colorful, easy to read, and caters to all ages. Also, we would like the design to take the whole page (not be centered) and can be viewed well on phone/tablet. Please see our outline for more information. Our motto/slogan is: Maplecrest Behavioral Healthcare- A step forward in your wellness journey, so the design should try to reflect that.
Updates

Project Deadline Extended
Reason: site in progress

Target Market(s)

Children through elderly

Industry/Entity Type

Medical

Logo Text

Stepping forward in your wellness journey

Number of Pages Required

1 page

Colors

Designer to choose colors to be used in the design.

Requirements
Must have
• Animation or moving pictures.
• Color.
• Concise.
• User friendly
• Diversity in the stock photos

```html
<!DOCTYPE html>
<html lang="en">
<head>
<meta charset="utf-8">
<title>Maplecrest Behavioral Healthcare</title>
<link href="https://fonts.googleapis.com/css2?family=Open+Sans:ital,wght@0,400;0,600;0,700;1,400;1,600&family=Oswald:wght@500;600&display=swap" rel="stylesheet">
<style>
:root{
  --teal:#27a3a6;
  --teal-dark:#2b6f6a;
  --teal-deep:#2c5f5c;
  --green:#8dc63f;
  --ink:#333;
  --text:#555;
  --grey-bg:#efefef;
  --footer:#333333;
  --white:#fff;
  --line:#c9c9c9;
}
*{box-sizing:border-box;margin:0;padding:0}
html,body{width:1200px;height:3093px;overflow:hidden}
body{font-family:'Open Sans',sans-serif;color:var(--text);background:var(--white)}
.btn{display:inline-flex;align-items:center;justify-content:center;border-radius:30px;color:var(--white);font-weight:700;text-transform:uppercase;font-size:15px;letter-spacing:.5px}
.btn-teal{background:var(--teal);width:178px;height:46px}
.btn-green{background:var(--green)}

/* header */
.site-header{height:142px;display:flex;align-items:center;padding:0 76px;position:relative}
.brand{display:flex;align-items:center;gap:16px}
.brand-dot{width:64px;height:64px;border-radius:50%;background:var(--teal)}
.brand-name{font-size:22px;font-weight:700;color:var(--teal);width:240px;line-height:1.2}
.info{position:absolute;top:40px;display:flex;gap:14px}
.info svg{flex:none;margin-top:2px}
.info-label{font-size:13px;font-weight:700;color:var(--green)}
.info-hours{left:690px}
.info-hours p{font-size:13px;color:var(--ink);line-height:1.6}
.info-hours .closed{color:var(--green)}
.info-phone{left:948px}
.info-phone .num{font-size:20px;font-weight:700;color:var(--green);margin-top:2px}

/* nav */
.main-nav{height:58px;background:var(--teal);display:flex;align-items:center;padding:0 76px;position:relative}
.main-nav a{height:58px;display:flex;align-items:center;padding:0 22px;color:var(--white);font-size:14px;font-weight:700;text-transform:uppercase;text-decoration:none}
.main-nav a.active{background:var(--green)}
.portal{position:absolute;left:885px;top:9px;width:240px;height:40px;border-radius:22px;background:var(--teal-deep);color:var(--white);display:flex;align-items:center;justify-content:center;gap:10px;font-weight:700;font-size:15px;text-transform:uppercase}

/* hero */
.hero{height:536px;position:relative;text-align:center;color:var(--white)}
.hero-photo{position:absolute;inset:0;background:linear-gradient(100deg,#b4a99c 0%,#8a8480 35%,#6f6e70 60%,#9c9a9a 100%)}
.hero-photo::after{content:"";position:absolute;inset:0;background:rgba(40,40,45,.35)}
.hero-content{position:relative;padding-top:190px}
.hero h1{font-family:'Oswald',sans-serif;font-weight:600;font-size:56px;line-height:1;text-transform:uppercase;letter-spacing:.5px}
.hero .tagline{font-size:25px;font-weight:700;text-transform:uppercase;margin-top:10px;letter-spacing:.5px}
.hero .btn{width:330px;height:56px;font-size:20px;margin-top:42px}

/* welcome */
.welcome{height:374px;text-align:center;padding-top:58px}
.section-title{font-size:28px;font-weight:700;color:var(--ink);text-transform:uppercase}
.welcome .section-title span{color:var(--teal)}
.welcome .lead{font-style:italic;font-weight:600;color:var(--teal);font-size:16px;line-height:1.6;width:980px;margin:22px auto 0}
.welcome .body{font-size:15px;line-height:1.8;width:1010px;margin:12px auto 0}
.welcome .btn{margin-top:36px}

/* services */
.services{height:636px;background:var(--teal-dark);text-align:center;padding-top:52px;color:var(--white)}
.services .section-title{color:var(--white)}
.service-grid{display:grid;grid-template-columns:repeat(3,360px);width:1080px;margin:34px auto 0}
.service{height:196px;display:flex;flex-direction:column;align-items:center;padding-top:10px;border-right:1px solid rgba(255,255,255,.2)}
.service:nth-child(3n){border-right:none}
.service:nth-child(-n+3){border-bottom:1px solid rgba(255,255,255,.2);height:184px}
.service:nth-child(n+4){padding-top:22px}
.service .icon{width:100px;height:100px;border:3px solid var(--white);border-radius:50%;display:flex;align-items:center;justify-content:center}
.service p{font-size:16px;font-weight:600;line-height:1.4;margin-top:18px}
.services .btn{width:182px;height:48px;margin-top:32px;font-size:14px}

/* faq */
.faq{height:497px;text-align:center;padding-top:44px}
.faq-cols{display:grid;grid-template-columns:512px 512px;gap:26px;width:1050px;margin:24px auto 0;text-align:left}
.faq-col h3{font-size:17px;font-weight:700;color:var(--green);text-transform:uppercase;text-align:center;margin-bottom:14px}
.faq-item{border:1px solid var(--line);border-radius:14px;padding:0 22px;margin-bottom:13px;min-height:47px;display:flex;flex-direction:column;justify-content:center;font-size:15px;color:var(--ink);position:relative}
.faq-item .toggle{position:absolute;right:20px;top:14px;width:16px;height:16px;background:var(--ink);border-radius:2px}
.faq-item .toggle::before,.faq-item .toggle::after{content:"";position:absolute;background:var(--white);left:3px;top:7px;width:10px;height:2px}
.faq-item .toggle::after{left:7px;top:3px;width:2px;height:10px}
.faq-item.open{height:92px;padding-top:4px}
.faq-item.open .q{color:var(--teal)}
.faq-item.open .toggle{background:var(--teal)}
.faq-item.open .toggle::after{display:none}
.faq-item .a{font-style:italic;font-size:14px;color:var(--text);margin-top:8px;line-height:1.5;padding-right:20px}
.faq .btn{width:178px;height:46px;margin-top:24px}

/* news */
.news{height:526px;background:linear-gradient(#fff,var(--grey-bg) 60%);text-align:center;padding-top:40px}
.news-grid{display:grid;grid-template-columns:repeat(3,331px);gap:29px;width:1051px;margin:26px auto 0;text-align:left}
.news-photo{height:194px;position:relative}
.news-date{position:absolute;left:0;right:0;bottom:0;height:36px;background:rgba(20,20,20,.85);color:var(--white);font-size:14px;font-weight:700;display:flex;align-items:center;justify-content:center;gap:8px}
.news-card h4{font-size:19px;font-weight:600;color:var(--teal);text-transform:uppercase;line-height:1.35;margin-top:16px}
.news-card p{font-size:15px;line-height:1.55;margin-top:12px;color:var(--ink)}
.news-card .more{display:block;color:var(--green);font-weight:700;font-size:15px;margin-top:16px}

/* footer */
.site-footer{height:324px;background:var(--footer);color:var(--white);position:relative;padding:34px 76px}
.footer-brand .brand-dot{width:56px;height:56px}
.footer-brand .brand-name{color:var(--white);font-size:18px;width:200px;margin-top:12px}
.copyright{font-size:12px;line-height:1.6;margin-top:14px}
.social{width:30px;height:30px;background:var(--green);border-radius:4px;margin-top:26px}
.f-col{position:absolute;top:46px}
.f-col h5{font-size:14px;font-weight:700;color:var(--teal);text-transform:uppercase;margin-bottom:8px}
.f-col li{list-style:none;font-size:13px;line-height:26.5px}
.col-site{left:361px}.col-about{left:598px}.col-email{left:850px;width:240px}
.f-input{height:38px;border-radius:20px;background:var(--white);color:var(--ink);font-size:12px;padding:0 18px;display:flex;align-items:center;margin-bottom:10px;width:240px}
.col-email .btn{width:106px;height:38px;font-size:14px;margin-left:134px}
</style>
</head>
<body>

<header class="site-header">
  <div class="brand">
    <div class="brand-dot"></div>
    <div class="brand-name">Maplecrest Behavioral Healthcare</div>
  </div>
  <div class="info info-hours">
    <svg width="24" height="24" viewBox="0 0 24 24"><circle cx="12" cy="12" r="10" fill="none" stroke="#555" stroke-width="2.5"/><path d="M12 6v6l4 2" fill="none" stroke="#555" stroke-width="2.5"/></svg>
    <div>
      <div class="info-label">HOURS:</div>
      <p>Mon - Sat 9:00am - 7:00pm</p>
      <p>Sun <span class="closed">Closed</span></p>
    </div>
  </div>
  <div class="info info-phone">
    <svg width="22" height="22" viewBox="0 0 24 24"><path d="M6.6 10.8a15 15 0 0 0 6.6 6.6l2.2-2.2c.3-.3.7-.4 1-.2 1.1.4 2.3.6 3.6.6.6 0 1 .4 1 1V20c0 .6-.4 1-1 1A17 17 0 0 1 3 4c0-.6.4-1 1-1h3.5c.6 0 1 .4 1 1 0 1.3.2 2.5.6 3.6.1.3 0 .7-.2 1z" fill="#555"/></svg>
    <div>
      <div class="info-label">PHONE:</div>
      <div class="num">1-800-555-0142</div>
    </div>
  </div>
</header>

<nav class="main-nav">
  <a class="active">Home</a><a>About Us</a><a>Services</a><a>Conditions We Treat</a><a>New Patients</a><a>Contact Us</a>
  <div class="portal">
    <svg width="14" height="16" viewBox="0 0 14 16"><circle cx="7" cy="4" r="4" fill="#fff"/><path d="M0 16c0-4 3-7 7-7s7 3 7 7z" fill="#fff"/></svg>
    Patient Portal
  </div>
</nav>

<section class="hero">
  <div class="hero-photo" role="img" aria-label="Photo of a counselor talking with a patient in a bright office"></div>
  <div class="hero-content">
    <h1>Maplecrest Behavioral Healthcare</h1>
    <p class="tagline">A step forward in your wellness journey</p>
    <span class="btn btn-green">Take a Screening</span>
  </div>
</section>

<section class="welcome">
  <h2 class="section-title">Welcome to <span>MBHC</span></h2>
  <p class="lead">We are Maplecrest Behavioral Healthcare, a mental health outpatient practice based in Georgia that sees diverse individuals and families from childhood to advanced age for a variety of conditions.</p>
  <p class="body">Aliquam molestie, mi et imperdiet euismod, dui purus auctor tellus, et interdum lacus lectus et ante. Sed accumsan sollicitudin sapien, sit amet adipiscing turpis gravida ac. In congue, neque ac lobortis volutpat, libero mauris varius mi, vitae suscipit ipsum ligula vitae risus. Duis aliquam nibh a dui iaculis viverra id a velit.</p>
  <span class="btn btn-teal">Read More</span>
</section>

<section class="services">
  <h2 class="section-title">Our Services</h2>
  <div class="service-grid">
    <div class="service">
      <div class="icon"><svg width="44" height="50" viewBox="0 0 44 50" fill="none" stroke="#fff" stroke-width="2.5"><rect x="4" y="6" width="36" height="42" rx="3"/><rect x="14" y="2" width="16" height="8" rx="2"/><path d="M10 30h7l3-7 4 12 3-5h7"/></svg></div>
      <p>Diagnostic Evaluation and<br>Treatment</p>
    </div>
    <div class="service">
      <div class="icon"><svg width="50" height="48" viewBox="0 0 50 48" fill="none" stroke="#fff" stroke-width="2.5"><path d="M14 46V36c-6-3-10-9-10-16C4 10 13 2 25 2s21 8 21 18c0 3-1 5-2 7l4 6-5 2v6h-8v5"/><circle cx="24" cy="18" r="8"/></svg></div>
      <p>Psychopharmacology</p>
    </div>
    <div class="service">
      <div class="icon"><svg width="40" height="50" viewBox="0 0 40 50" fill="none" stroke="#fff" stroke-width="2.5"><path d="M16 2v10c0 6 4 8 10 8s10 4 10 12-6 16-16 16S4 44 4 38s4-8 8-8"/></svg></div>
      <p>Bariatric Pre-Surgical<br>Consultation</p>
    </div>
    <div class="service">
      <div class="icon"><svg width="48" height="48" viewBox="0 0 48 48" fill="none" stroke="#fff" stroke-width="2.5"><circle cx="20" cy="6" r="4"/><path d="M20 12v16h14l6 12"/><path d="M14 22a12 12 0 1 0 16 16"/></svg></div>
      <p>Disability and<br>Work-Related Reports</p>
    </div>
    <div class="service">
      <div class="icon"><svg width="48" height="48" viewBox="0 0 48 48" fill="none" stroke="#fff" stroke-width="2.5"><circle cx="18" cy="8" r="5"/><path d="M10 46V22h14v24M24 28h14M38 22v24"/><circle cx="38" cy="12" r="3"/></svg></div>
      <p>Early Childhood<br>Assessments</p>
    </div>
    <div class="service">
      <div class="icon"><svg width="48" height="48" viewBox="0 0 48 48" fill="none" stroke="#fff" stroke-width="2.5"><path d="M8 40l22-22 6 6-22 22H8z"/><path d="M30 12l12 12M36 6l6 6M4 44l4-4"/></svg></div>
      <p>Substance Abuse<br>Assessments</p>
    </div>
  </div>
  <span class="btn btn-green">View All Services</span>
</section>

<section class="faq">
  <h2 class="section-title">FAQ's</h2>
  <div class="faq-cols">
    <div class="faq-col">
      <h3>Office Visit:</h3>
      <div class="faq-item"><span class="q">What do I need to bring with me to my first visit?</span><span class="toggle"></span></div>
      <div class="faq-item open"><span class="q">How long do I have to wait to be seen?</span><span class="toggle"></span><span class="a">We try to have very little wait time for your convenience.</span></div>
      <div class="faq-item"><span class="q">What types of insurance do you accept?</span><span class="toggle"></span></div>
    </div>
    <div class="faq-col">
      <h3>Signs that you may need to schedule a visit.</h3>
      <div class="faq-item"><span class="q">Why is my child not doing well in school?</span><span class="toggle"></span></div>
      <div class="faq-item open"><span class="q">I feel sad, tired and I do not have energy. Is that normal?</span><span class="toggle"></span><span class="a">No, If you have these feeling for a long period of time, you may be suffering from depression or other mood disorders.</span></div>
      <div class="faq-item"><span class="q">I am have trouble with my child. Do you do therapy for children?</span><span class="toggle"></span></div>
    </div>
  </div>
  <span class="btn btn-teal">Read All FAQ</span>
</section>

<section class="news">
  <h2 class="section-title">Latest News</h2>
  <div class="news-grid">
    <article class="news-card">
      <div class="news-photo" role="img" aria-label="Photo of an older woman and a young girl in a therapy session" style="background:linear-gradient(120deg,#d8cfc4,#a9b8bf)"><div class="news-date">&#9638; SEP 20, 2017</div></div>
      <h4>Nam fermentum vestibulum purus id aliquet nibh</h4>
      <p>Aliquam molestie, mi et imperdiet euismod, du ante ipsum primis in faucibus orci luctus et ultrices posuere cubilia..</p>
      <span class="more">Read More</span>
    </article>
    <article class="news-card">
      <div class="news-photo" role="img" aria-label="Photo of a stressed man holding his head at a desk" style="background:linear-gradient(120deg,#c9c6c2,#7d7b78)"><div class="news-date">&#9638; SEP 20, 2017</div></div>
      <h4>Nam fermentum vestibulum purus id aliquet nibh</h4>
      <p>Aliquam molestie, mi et imperdiet euismod, du ante ipsum primis in faucibus orci luctus et ultrices posuere cubilia..</p>
      <span class="more">Read More</span>
    </article>
    <article class="news-card">
      <div class="news-photo" role="img" aria-label="Photo of a therapist speaking with a young man in a bright office" style="background:linear-gradient(120deg,#e6e9ea,#9fb0b8)"><div class="news-date">&#9638; SEP 20, 2017</div></div>
      <h4>Nam fermentum vestibulum purus id aliquet nibh</h4>
      <p>Aliquam molestie, mi et imperdiet euismod, du ante ipsum primis in faucibus orci luctus et ultrices posuere cubilia..</p>
      <span class="more">Read More</span>
    </article>
  </div>
</section>

<footer class="site-footer">
  <div class="footer-brand">
    <div class="brand-dot"></div>
    <div class="brand-name">Maplecrest Behavioral Healthcare</div>
    <p class="copyright">Copyright © 2017. Company Name<br>All Right Reserved</p>
    <div class="social"></div>
  </div>
  <div class="f-col col-site">
    <h5>Site Map</h5>
    <ul><li>Home</li><li>About us</li><li>Services</li><li>Condition We Treat</li><li>New Patients</li><li>Contact Us</li></ul>
  </div>
  <div class="f-col col-about">
    <h5>About Us</h5>
    <ul><li>Vision &amp; Mission</li><li>Our Providers</li><li>Health Insurance Plans</li><li>Office Policies</li><li>Prescription Refills</li><li>Online Payment?</li><li>HIPPA</li><li>FAQ</li></ul>
  </div>
  <div class="f-col col-email">
    <h5>Email Subscribe</h5>
    <div class="f-input">Enter Name</div>
    <div class="f-input">Enter Email Address</div>
    <span class="btn btn-green">Sign Up</span>
  </div>
</footer>

</body>
</html>
```